Modern looking signage for dental office.

Exterior signage for passing cars
Updates
Need extra days to review
Target Market(s)
Cars passing by
Font styles to use
Sans Serif
Colors
3276b5
Requirements
Must have
- Logo
- OPEN ON SUTURDAY AND SUNDAY
- NIGHT CLINIC AVAILABLE
- PLEASE USE THE FONT TYPE IN FILE 4 UPLOADED BELOW.
- (847) 302-7469
- Modern looking

```html
<!DOCTYPE html>
<html lang="en">
<head>
<meta charset="utf-8">
<title>Peak Dental – Exterior Sign</title>
<link href="https://fonts.googleapis.com/css2?family=Josefin+Sans:wght@300&family=Encode+Sans+Condensed:wght@500&family=Didact+Gothic&display=swap" rel="stylesheet">
<style>
  :root {
    --teal: #137a8c;
    --ink: #3b3838;
    --stripe: #3e3a3a;
    --panel-light: #ffffff;
    --panel-shade: #e4e4e4;
    --backdrop: #eef0f1;
  }
  html, body {
    margin: 0;
    width: 1200px;
    height: 1200px;
    overflow: hidden;
    background: var(--backdrop);
  }
  .sign {
    position: absolute;
    left: 50px;
    top: 260px;
    width: 1100px;
    height: 680px;
    background: radial-gradient(ellipse at 45% 50%, var(--panel-light) 0%, #f3f3f3 55%, var(--panel-shade) 100%);
    box-shadow: 0 6px 24px rgba(0,0,0,0.12);
    overflow: hidden;
  }
  .sign-shapes {
    position: absolute;
    inset: 0;
  }
  .brand {
    position: absolute;
    left: 100px;
    top: 64px;
    display: flex;
    align-items: center;
    gap: 28px;
    white-space: nowrap;
  }
  .brand-circle {
    flex: 0 0 auto;
    width: 140px;
    height: 140px;
    border: 3px solid var(--ink);
    border-radius: 50%;
    box-sizing: border-box;
  }
  .brand-name {
    font-family: "Josefin Sans", sans-serif;
    font-weight: 300;
    font-size: 100px;
    line-height: 1;
    color: var(--ink);
    letter-spacing: 1px;
    padding-top: 14px;
    white-space: nowrap;
  }
  .tagline {
    position: absolute;
    left: 300px;
    top: 212px;
    font-family: "Encode Sans Condensed", sans-serif;
    font-weight: 500;
    font-size: 40px;
    line-height: 1;
    color: var(--ink);
    letter-spacing: 0.5px;
    white-space: nowrap;
  }
  .hours {
    position: absolute;
    left: 0;
    width: 1000px;
    top: 318px;
    text-align: center;
    font-family: "Didact Gothic", sans-serif;
    font-size: 60px;
    line-height: 74px;
    color: var(--teal);
    letter-spacing: 3px;
    white-space: nowrap;
  }
  .phone {
    position: absolute;
    left: 36px;
    top: 574px;
    display: flex;
    align-items: center;
    gap: 16px;
    font-family: "Didact Gothic", sans-serif;
    font-size: 46px;
    line-height: 1;
    color: var(--ink);
    letter-spacing: 2px;
    white-space: nowrap;
  }
  .phone-icon { width: 50px; height: 50px; }
  .night-clinic {
    position: absolute;
    right: 60px;
    top: 556px;
    text-align: right;
    font-family: "Didact Gothic", sans-serif;
    font-size: 52px;
    line-height: 60px;
    color: #ffffff;
    letter-spacing: 4px;
    white-space: nowrap;
  }
</style>
</head>
<body>
  <div class="sign">
    <svg class="sign-shapes" width="1100" height="680" viewBox="0 0 1100 680">
      <path class="corner-accent" d="M0 0 H165 Q55 85 0 215 Z" fill="var(--teal)"/>
      <path class="corner-swoosh" d="M165 0 Q55 85 0 215 L0 240 Q70 95 200 0 Z" fill="#ffffff"/>
      <rect class="footer-light" x="0" y="540" width="1100" height="140" fill="#ffffff"/>
      <polygon class="footer-stripe" points="418,540 446,540 532,680 504,680" fill="var(--stripe)"/>
      <polygon class="footer-band" points="468,540 1100,540 1100,680 556,680" fill="var(--teal)"/>
    </svg>

    <div class="brand">
      <div class="brand-circle"></div>
      <div class="brand-name">PEAK DENTAL</div>
    </div>
    <div class="tagline">MODERN GENERAL DENTISTRY</div>

    <div class="hours">OPEN ON<br>SATURDAY AND SUNDAY</div>

    <div class="phone">
      <svg class="phone-icon" viewBox="0 0 50 50">
        <circle cx="25" cy="25" r="22" fill="none" stroke="var(--teal)" stroke-width="3"/>
        <path d="M17 13 l5 -1 l3 8 l-3 2 q2 5 7 8 l2 -3 l8 3 l-1 5 q-2 3 -6 2 q-14 -5 -17 -18 q0 -4 2 -6 z" fill="var(--teal)"/>
      </svg>
      <span>(847) 302-7469</span>
    </div>

    <div class="night-clinic">NIGHT CLINIC<br>AVAILABLE</div>
  </div>
</body>
</html>
```